Copper Lantern

Need a business card for our restaurant. Restaurant and Bar in the mountains of North Idaho. Rustic looking card

rustic design, wood and metal looking, primarily neutral colors

• Name, address, phone number, website, email address

```html
<!DOCTYPE html>
<html lang="en">
<head>
<meta charset="utf-8">
<title>Copper Lantern – Business Card</title>
<link rel="stylesheet" href="https://fonts.googleapis.com/css2?family=Montserrat:wght@400;700&display=swap">
<style>
  :root {
    --stage: #2b2b2b;
    --card: #141414;
    --card-edge: #1e1e1e;
    --ink: #ffffff;
    --ink-soft: #d9d9d9;
    --emboss: #3a3d3c;
    --emboss-light: #5a605e;
    --spot-dark: #050505;
    --spot-sheen: #39423f;
  }
  * { box-sizing: border-box; margin: 0; padding: 0; }
  html, body { width: 1200px; height: 875px; overflow: hidden; }
  body {
    background: var(--stage);
    font-family: "Montserrat", sans-serif;
    display: flex;
    align-items: center;
    justify-content: center;
    gap: 40px;
  }
  .card {
    position: relative;
    width: 560px;
    height: 320px;
    background: var(--card);
    border-radius: 22px;
    border: 1px solid var(--card-edge);
    box-shadow: 0 18px 40px rgba(0,0,0,.45);
    overflow: hidden;
  }

  /* Front: embossed brand mark */
  .card--front {
    display: flex;
    align-items: center;
    justify-content: center;
  }
  .brand-emboss {
    display: flex;
    align-items: center;
    gap: 14px;
  }
  .brand-emboss .brand-dot {
    width: 46px; height: 46px;
    border-radius: 50%;
    border: 2px solid var(--emboss-light);
  }
  .brand-emboss .brand-name {
    font-weight: 700;
    font-size: 30px;
    letter-spacing: 3px;
    text-transform: uppercase;
    color: var(--emboss-light);
  }

  /* Back: contact side */
  .card--back { padding: 34px 36px; }
  .brand-mark {
    display: flex;
    align-items: center;
    gap: 10px;
  }
  .brand-mark .brand-dot {
    width: 28px; height: 28px;
    border-radius: 50%;
    border: 2px solid var(--ink);
  }
  .brand-mark .brand-name {
    font-weight: 700;
    font-size: 16px;
    letter-spacing: 1.5px;
    text-transform: uppercase;
    color: var(--ink);
  }
  .person { margin-top: 26px; }
  .person__name {
    font-weight: 700;
    font-size: 24px;
    color: var(--ink);
    line-height: 1.1;
  }
  .person__role {
    font-size: 14px;
    color: var(--ink-soft);
    margin-top: 2px;
  }
  .address {
    margin-top: 14px;
    font-size: 14px;
    line-height: 1.3;
    color: var(--ink-soft);
    font-style: normal;
  }
  .contacts {
    list-style: none;
    margin-top: 14px;
    font-size: 14px;
    color: var(--ink-soft);
  }
  .contacts li {
    display: flex;
    align-items: center;
    gap: 10px;
    line-height: 1.55;
  }
  .contacts svg { width: 14px; height: 14px; fill: var(--ink); flex: none; }
  .spot-art {
    position: absolute;
    right: 40px;
    top: 34px;
    width: 190px;
    height: 250px;
    border-radius: 14px;
    background: radial-gradient(ellipse at 40% 70%, var(--spot-sheen), var(--spot-dark) 70%);
  }
</style>
</head>
<body>

  <section class="card card--front" aria-label="Card front">
    <div class="brand-emboss">
      <span class="brand-dot"></span>
      <span class="brand-name">Copper Lantern</span>
    </div>
  </section>

  <section class="card card--back" aria-label="Card back">
    <div class="brand-mark">
      <span class="brand-dot"></span>
      <span class="brand-name">Copper Lantern</span>
    </div>

    <div class="person">
      <p class="person__name">Mara Ellison</p>
      <p class="person__role">Managing Director</p>
    </div>

    <address class="address">48 Ridge Road,<br>Pinecrest, USA</address>

    <ul class="contacts">
      <li>
        <svg viewBox="0 0 24 24"><path d="M6.6 10.8a15 15 0 0 0 6.6 6.6l2.2-2.2a1 1 0 0 1 1-.25 11.4 11.4 0 0 0 3.6.57 1 1 0 0 1 1 1V20a1 1 0 0 1-1 1A17 17 0 0 1 3 4a1 1 0 0 1 1-1h3.5a1 1 0 0 1 1 1c0 1.25.2 2.45.57 3.57a1 1 0 0 1-.25 1z"/></svg>
        (08) 4431 2087
      </li>
      <li>
        <svg viewBox="0 0 24 24"><path d="M2 5h20v14H2zm2 2v.5l8 5 8-5V7l-8 5z"/></svg>
        hello@copperlantern.com
      </li>
      <li>
        <svg viewBox="0 0 24 24"><circle cx="12" cy="12" r="10"/></svg>
        www.copperlantern.com
      </li>
    </ul>

    <div class="spot-art" role="img" aria-label="Large glossy spot-varnish animal illustration"></div>
  </section>

</body>
</html>
```